Brell Stone Company Business Cards

Front and Back Business Card - logo and text setup - cool design. I need workable photoshop or illustrator files so I can setup each employee card with design that is created
Updates

Hi everyone, thank you for the great entries. Please no more white and blue cards - there are so many already - black and silver only now please. thanks!

Target Market(s)

Construction Industry - Facility Managers

Industry/Entity Type

Construction

Contact Information for Business Card

I really like contemporary simplistic looks - clean neat....not opposed to seeing some black backrounds

Requirements
Must have
• Logo/website address with design on front only - www.brellstone-example.com (logo attached)
• Back:
• Name/Title/Company Address/Phone/email address
Nice to have
• Cool design
Should not have
• Nothing gimmicky like Fire or Water - since we are a Fire Protection company - it has all been done

```html
<!DOCTYPE html>
<html lang="en">
<head>
<meta charset="utf-8">
<title>Brell Stone Company – Business Cards</title>
<link rel="stylesheet" href="https://fonts.googleapis.com/css2?family=Lato:wght@300;400;900&family=Oswald:wght@600&display=swap">
<style>
  :root {
    --backdrop: #151517;
    --card: #262628;
    --card-edge: #2c2c2e;
    --silver: #d9d9db;
    --silver-dim: #9c9ca0;
    --text: #e6e6e8;
    --accent: #34427a;
    --divider: #7a7a7e;
  }
  * { margin: 0; padding: 0; box-sizing: border-box; }
  html, body { width: 1200px; height: 912px; overflow: hidden; }
  body {
    background: var(--backdrop);
    position: relative;
    font-family: "Lato", sans-serif;
    color: var(--text);
  }
  .card {
    position: absolute;
    width: 540px;
    height: 310px;
    background: linear-gradient(160deg, var(--card-edge), var(--card));
    box-shadow: 0 18px 40px rgba(0,0,0,.55);
    overflow: hidden;
  }
  /* Front */
  .card--front { left: 60px; top: 100px; }
  .front-brand {
    position: absolute;
    left: 0; right: 0; top: 104px;
    text-align: center;
    font-family: "Lato", sans-serif;
    font-weight: 900;
    font-size: 54px;
    letter-spacing: -1px;
    color: var(--silver);
    line-height: 1;
  }
  .front-brand-mark {
    display: inline-block;
    width: 16px; height: 16px;
    background: var(--silver);
    margin-left: 10px;
    vertical-align: baseline;
  }
  .front-url {
    position: absolute;
    left: 0; right: 0; top: 222px;
    text-align: center;
    font-size: 16px;
    font-weight: 400;
    letter-spacing: .5px;
    color: var(--text);
  }
  /* Back */
  .card--back { left: 600px; top: 500px; }
  .card-band {
    position: absolute;
    left: 0; right: 0; bottom: 0;
    height: 7px;
    background: var(--accent);
  }
  .person {
    position: absolute;
    right: 300px;
    top: 118px;
    text-align: right;
  }
  .person-name {
    font-family: "Oswald", sans-serif;
    font-weight: 600;
    font-size: 23px;
    letter-spacing: .3px;
    color: #f2f2f2;
    text-transform: uppercase;
    white-space: nowrap;
  }
  .person-title {
    font-size: 17px;
    font-weight: 300;
    color: var(--accent);
    filter: brightness(1.25);
    margin-top: 2px;
  }
  .divider {
    position: absolute;
    left: 258px; top: 86px;
    width: 1px; height: 120px;
    background: var(--divider);
  }
  .contact {
    position: absolute;
    left: 278px; top: 90px;
    font-size: 13px;
    font-weight: 300;
    line-height: 1.4;
  }
  .contact-address { margin-bottom: 12px; }
  .contact-list { list-style: none; }
  .contact-list li { display: flex; align-items: center; gap: 9px; }
  .contact-list svg { width: 11px; height: 11px; flex: none; }
</style>
</head>
<body>
  <section class="card card--front">
    <div class="front-brand">Brell Stone<span class="front-brand-mark"></span></div>
    <p class="front-url">www.brellstone-example.com</p>
  </section>

  <section class="card card--back">
    <div class="person">
      <p class="person-name">Dana Marlow Ellis</p>
      <p class="person-title">President</p>
    </div>
    <div class="divider"></div>
    <div class="contact">
      <p class="contact-address">48 Harbor Works Road<br>Millbrook, NY 10000</p>
      <ul class="contact-list">
        <li>
          <svg viewBox="0 0 12 12" aria-hidden="true"><path fill="#5a68a8" d="M2.4 1h2l1 2.6-1.3 1a6.5 6.5 0 0 0 3.3 3.3l1-1.3 2.6 1v2c0 .8-.6 1.4-1.4 1.4A9.6 9.6 0 0 1 1 2.4C1 1.6 1.6 1 2.4 1z"/></svg>
          (555) 014-2290
        </li>
        <li>
          <svg viewBox="0 0 12 12" aria-hidden="true"><rect x="1" y="2.5" width="10" height="7" fill="#5a68a8"/><path d="M1 2.5 6 6.5 11 2.5" fill="none" stroke="#262628" stroke-width="1"/></svg>
          info@brellstone-example.com
        </li>
        <li>
          <svg viewBox="0 0 12 12" aria-hidden="true"><g fill="none" stroke="#5a68a8" stroke-width="1"><circle cx="6" cy="6" r="5"/><ellipse cx="6" cy="6" rx="2.2" ry="5"/><path d="M1 6h10M2 3.5h8M2 8.5h8"/></g></svg>
          www.brellstone-example.com
        </li>
      </ul>
    </div>
    <div class="card-band"></div>
  </section>
</body>
</html>
```